Brightwave Reach - Business Card

We need a business card for a Social Media Marketing company that specializes in online marketing for small businesses in Canada using common Social Media platforms such as Pixlora, Chatterly, Blinkpost & Quibber.

I have uploaded a copy of our logo which I would like utilized in the business card. We would like the business card to be modern yet classy design.

Our website is www.brightwavereach.ca

Industry/Entity Type

Marketing

Contact Information for Business Card

Email: info@brightwavereach.ca
Website: www.brightwavereach.ca
Telephone: 604-555-0193

Colors

Designer to choose colors to be used in the design.

Requirements
Must have
• Social Media icons on reverse
• Please add some designs with color.

```html
<!DOCTYPE html>
<html lang="en">
<head>
<meta charset="utf-8">
<title>Brightwave Reach – Business Card</title>
<link href="https://fonts.googleapis.com/css2?family=Lato:wght@400;700;900&display=swap" rel="stylesheet">
<style>
  :root {
    --stage: #e4e4e4;
    --card-dark: #3e4143;
    --card-light: #ffffff;
    --ink: #2b2b2b;
    --ink-soft: #444444;
    --on-dark: #ffffff;
    --rule: #3a3a3a;
  }
  * { box-sizing: border-box; margin: 0; padding: 0; }
  html, body { width: 1200px; height: 900px; overflow: hidden; }
  body {
    background: var(--stage);
    font-family: "Lato", sans-serif;
    position: relative;
  }
  .card {
    position: absolute;
    left: 250px;
    width: 700px;
    height: 400px;
    box-shadow: 0 6px 18px rgba(0,0,0,.18);
  }
  .card--back { top: 30px; background: var(--card-dark); color: var(--on-dark); }
  .card--front { top: 470px; background: var(--card-light); color: var(--ink); }

  /* brand lockup */
  .brand {
    position: absolute;
    display: flex;
    align-items: center;
    gap: 14px;
    font-weight: 900;
    text-transform: uppercase;
    letter-spacing: 1px;
    line-height: 1;
  }
  .brand__mark { border: 4px solid currentColor; flex: none; }
  .card--back .brand { left: 0; right: 0; top: 90px; justify-content: center; font-size: 44px; }
  .card--back .brand__mark { width: 44px; height: 44px; }
  .card--front .brand { left: 40px; top: 160px; width: 250px; font-size: 30px; color: var(--ink-soft); flex-wrap: nowrap; }
  .card--front .brand__mark { width: 32px; height: 32px; }
  .brand__name { display: block; }

  /* social row */
  .socials {
    position: absolute;
    left: 0; right: 0; top: 220px;
    display: flex;
    justify-content: center;
    gap: 70px;
    list-style: none;
  }
  .socials__item { display: flex; flex-direction: column; align-items: center; gap: 10px; font-size: 15px; font-weight: 700; }
  .socials__tile { width: 52px; height: 52px; background: var(--on-dark); border-radius: 8px; }

  /* front details */
  .divider { position: absolute; left: 330px; top: 110px; width: 2px; height: 180px; background: var(--rule); }
  .person { position: absolute; left: 380px; top: 120px; }
  .person__name { font-size: 32px; font-weight: 700; color: var(--ink-soft); }
  .person__role { font-size: 18px; color: var(--ink-soft); margin-top: 2px; }
  .contacts { list-style: none; margin-top: 22px; }
  .contacts li { display: flex; align-items: center; gap: 14px; font-size: 20px; color: #111; line-height: 30px; }
  .contacts svg { width: 16px; height: 16px; flex: none; fill: var(--ink-soft); }
</style>
</head>
<body>

<section class="card card--back" aria-label="Card reverse">
  <div class="brand">
    <span class="brand__mark"></span>
    <span class="brand__name">Brightwave Reach</span>
  </div>
  <ul class="socials">
    <li class="socials__item"><span class="socials__tile"></span>Chatterly</li>
    <li class="socials__item"><span class="socials__tile"></span>Pixlora</li>
    <li class="socials__item"><span class="socials__tile"></span>Quibber</li>
    <li class="socials__item"><span class="socials__tile"></span>Blinkpost</li>
  </ul>
</section>

<section class="card card--front" aria-label="Card front">
  <div class="brand">
    <span class="brand__mark"></span>
    <span class="brand__name">Brightwave<br>Reach</span>
  </div>
  <div class="divider"></div>
  <div class="person">
    <h1 class="person__name">Daniel Mercer</h1>
    <p class="person__role">Manager</p>
    <ul class="contacts">
      <li>
        <svg viewBox="0 0 16 16" aria-hidden="true"><path d="M3.5 1l3 3-1.8 1.8a9 9 0 0 0 5.5 5.5L12 9.5l3 3-2 2C7 14 2 9 1.5 3z"/></svg>
        604-555-0193
      </li>
      <li>
        <svg viewBox="0 0 16 16" aria-hidden="true"><path d="M1 3h14v10H1z M1.8 3.8L8 9l6.2-5.2" fill="none" stroke="#444" stroke-width="1.5"/></svg>
        info@brightwavereach.ca
      </li>
      <li>
        <svg viewBox="0 0 16 16" aria-hidden="true"><circle cx="8" cy="8" r="7" fill="none" stroke="#444" stroke-width="1.4"/><ellipse cx="8" cy="8" rx="3" ry="7" fill="none" stroke="#444" stroke-width="1.2"/><path d="M1 8h14" stroke="#444" stroke-width="1.2"/></svg>
        www.brightwavereach.ca
      </li>
    </ul>
  </div>
</section>

</body>
</html>
```